Business Card Design Project : Ridgeline Press

In preparation for market launch, Tamarind's Ridgeline Press require the development of a business card. Ridgeline Press is a Community online publishing web portal. We provide the the city of Whistler located in B.C. (Canada) business directories, News, Classified ads, News, Events and blogs etc.

The main focus of the brand is to help local businesses to corporate with their online advertisement and marketing. Meeting our clients face to face is a must (B2B).

Target Market(s)

The target market is B2B customers. Business Owners to Marketing, advertising Managers

Industry/Entity Type

Business

Requirements
Must have
• - The business card will be two sided.
the BACK side will have our logo which consist of (icon, url,slogan) submited. The logo will be middle and centred.

The FRONT side should have company details:

Company Legal Name: TAMARIND RIDGELINE MEDIA

Owen Farsk
Director of Sales & Marketing

www.tamarindridgeline.biz
owen@tamarindridgeline.biz

Phone: 604 317 8842
#2714 - 582 E. Halvern St.
Vancouver, B.C. V7K2R4 Canada
Nice to have
• - For the "FRONT" side of our business card. You can separate or re-arrange with our logo components (icon, logo,slogan). It does not have to be together.

Also our company legal name is rather long so arrange or organize the name in a way to make it shorter. Your experience and creativity will have to come in play.
Should not have
• should not have other colors beside logo color and black text (2 colors). Also nothing Three dimensional

```html
<!DOCTYPE html>
<html lang="en">
<head>
<meta charset="utf-8">
<title>Tamarind Ridgeline Press – Business Card Options</title>
<link rel="stylesheet" href="https://fonts.googleapis.com/css2?family=Della+Respira&family=Open+Sans:wght@400;700&display=swap">
<style>
  :root {
    --brand-blue: #0a7ad1;
    --ink: #111111;
    --paper: #ffffff;
    --stack-grey: #8c8c8c;
    --stack-edge: #333333;
  }
  * { box-sizing: border-box; margin: 0; padding: 0; }
  html, body { width: 1200px; height: 914px; overflow: hidden; background: var(--paper); }
  body { position: relative; font-family: "Open Sans", Arial, sans-serif; color: var(--ink); }

  .option { position: absolute; width: 590px; height: 440px; }
  .option--one   { left: 6px;   top: 4px; }
  .option--two   { left: 612px; top: 14px; }
  .option--three { left: 2px;   top: 488px; }
  .option--four  { left: 608px; top: 496px; }

  .stack {
    position: absolute; left: 10px; top: 8px; width: 566px; height: 330px;
    background: var(--stack-grey); border: 2px solid var(--stack-edge);
    transform: rotate(1.6deg);
  }
  .card {
    position: absolute; left: 12px; top: 24px; width: 560px; height: 318px;
    background: var(--paper); overflow: hidden;
    transform: rotate(-0.8deg);
  }
  .card__field { position: absolute; inset: 0; }

  .brand { position: absolute; top: 26px; }
  .brand--left  { left: 24px; text-align: left; }
  .brand--right { right: 24px; text-align: right; }
  .brand__name { display: flex; align-items: center; gap: 10px; font-size: 24px; font-weight: 400; color: var(--paper); line-height: 1; }
  .brand--right .brand__name { justify-content: flex-end; }
  .brand__mark { width: 18px; height: 18px; border-radius: 50%; background: var(--paper); flex: none; }
  .brand__slogan { font-size: 11.5px; letter-spacing: 1.2px; color: var(--paper); margin-top: 4px; text-align: right; }

  .holder { position: absolute; left: 0; right: 0; top: 100px; text-align: center; }
  .holder__name { font-family: "Della Respira", Georgia, serif; font-size: 42px; color: var(--ink); letter-spacing: 1px; line-height: 1; }
  .holder__title { font-size: 13px; font-weight: 700; letter-spacing: 3.4px; color: var(--paper); margin-top: 16px; }

  .contact {
    position: absolute; right: 20px; top: 200px; text-align: right;
    font-size: 11.5px; font-weight: 700; line-height: 17px; color: var(--paper); letter-spacing: 0.4px;
  }
  .online { position: absolute; left: 30px; top: 250px; font-size: 12.5px; line-height: 17px; color: var(--ink); }
  .online b { font-weight: 700; }
  .online--blue { color: var(--brand-blue); }

  .option__number {
    position: absolute; left: 262px; top: 360px; width: 64px; height: 64px;
    border: 2px solid var(--ink); border-radius: 50%;
    font-size: 42px; line-height: 58px; text-align: center; font-weight: 400;
  }
</style>
</head>
<body>

<section class="option option--one">
  <div class="stack"></div>
  <article class="card">
    <svg class="card__field" width="560" height="318" viewBox="0 0 560 318" aria-hidden="true">
      <path d="M0 0H560V290C430 282 300 256 190 226C110 206 50 186 0 178Z" fill="var(--brand-blue)"/>
    </svg>
    <div class="brand brand--left">
      <div class="brand__name"><span class="brand__mark"></span>Tamarind Ridgeline Press</div>
      <div class="brand__slogan">Local news for local business</div>
    </div>
    <div class="holder">
      <div class="holder__name">Owen Farsk</div>
      <div class="holder__title">Director of Sales &amp; Marketing</div>
    </div>
    <div class="contact">Phone: 604 317 8842<br>#2714 - 582 E. Halvern St.<br>Vancouver, B.C. V7K2R4 Canada</div>
    <div class="online">www.<b>tamarindridgeline</b>.biz<br><b>owen@tamarindridgeline</b>.biz</div>
  </article>
  <div class="option__number">1</div>
</section>

<section class="option option--two">
  <div class="stack"></div>
  <article class="card">
    <svg class="card__field" width="560" height="318" viewBox="0 0 560 318" aria-hidden="true">
      <path d="M0 0H560V290C430 282 300 256 190 226C110 206 50 186 0 178Z" fill="var(--brand-blue)"/>
    </svg>
    <div class="brand brand--left">
      <div class="brand__name"><span class="brand__mark"></span>Tamarind Ridgeline Press</div>
      <div class="brand__slogan">Local news for local business</div>
    </div>
    <div class="holder">
      <div class="holder__name">Owen Farsk</div>
      <div class="holder__title">Director of Sales &amp; Marketing</div>
    </div>
    <div class="contact">Phone: 604 317 8842<br>#2714 - 582 E. Halvern St.<br>Vancouver, B.C. V7K2R4 Canada</div>
    <div class="online online--blue">www.<b>tamarindridgeline</b>.biz<br><b>owen@tamarindridgeline</b>.biz</div>
  </article>
  <div class="option__number">2</div>
</section>

<section class="option option--three">
  <div class="stack"></div>
  <article class="card">
    <svg class="card__field" width="560" height="318" viewBox="0 0 560 318" aria-hidden="true">
      <path d="M0 0H560V290C430 282 300 256 190 226C110 206 50 186 0 178Z" fill="var(--brand-blue)"/>
    </svg>
    <div class="brand brand--right">
      <div class="brand__name"><span class="brand__mark"></span>Tamarind Ridgeline Press</div>
      <div class="brand__slogan">Local news for local business</div>
    </div>
    <div class="holder">
      <div class="holder__name">Owen Farsk</div>
      <div class="holder__title">Director of Sales &amp; Marketing</div>
    </div>
    <div class="contact">Phone: 604 317 8842<br>#2714 - 582 E. Halvern St.<br>Vancouver, B.C. V7K2R4 Canada</div>
    <div class="online">www.<b>tamarindridgeline</b>.biz<br><b>owen@tamarindridgeline</b>.biz</div>
  </article>
  <div class="option__number">3</div>
</section>

<section class="option option--four">
  <div class="stack"></div>
  <article class="card">
    <svg class="card__field" width="560" height="318" viewBox="0 0 560 318" aria-hidden="true">
      <path d="M0 0H560V290C430 282 300 256 190 226C110 206 50 186 0 178Z" fill="var(--brand-blue)"/>
    </svg>
    <div class="brand brand--right">
      <div class="brand__name"><span class="brand__mark"></span>Tamarind Ridgeline Press</div>
      <div class="brand__slogan">Local news for local business</div>
    </div>
    <div class="holder">
      <div class="holder__name">Owen Farsk</div>
      <div class="holder__title">Director of Sales &amp; Marketing</div>
    </div>
    <div class="contact">Phone: 604 317 8842<br>#2714 - 582 E. Halvern St.<br>Vancouver, B.C. V7K2R4 Canada</div>
    <div class="online online--blue">www.<b>tamarindridgeline</b>.biz<br><b>owen@tamarindridgeline</b>.biz</div>
  </article>
  <div class="option__number">4</div>
</section>

</body>
</html>
```